Brightwell Supports

We need an updated website that captures the comprehensive services and supports we provide to persons with developmental disabilities. We need a website design that educates families about the services we provide. We would also need a website that is user-friendly so that we could periodically update training schedules and ongoing programming.

• Thank you for submitting designs.  A few things I am hoping to see offered in the website:
• Front page highlights the services we offer (host homes, family caregiver, day program, employment program, SLS program, supported apartment program, behavior/clinical program)
• Front page also highlights any new programs we want to make prominent:  family caregiver, future restaurant employment openings, etc...
• Interactive Training Calendar
• Employee Resources page (link to carevo, email login, etc.)
• Uniform provider application for host home providers
• Information on agency - history, goals, etc.
• Contact Information/Location

 

Fun things to include:

• Client Highlights (featuring a client story each month, etc...)
• Employee highlights (featuring a staff member...)
• link to other Brightwell business pages (Brightwell Therapy and Brightwell Restaurant)

```html
<!DOCTYPE html>
<html lang="en">
<head>
<meta charset="utf-8">
<title>Brightwell Supports</title>
<link href="https://fonts.googleapis.com/css2?family=Source+Sans+3:wght@400;600&family=Tinos:wght@400&display=swap" rel="stylesheet">
<style>
:root{
  --wine:#7c2128;
  --wine-dark:#6a1a20;
  --page:#f4f4f4;
  --panel:#ffffff;
  --line:#dcdcdc;
  --ink:#3e3e3e;
  --muted:#666666;
  --dot:#b5b5b5;
}
*{margin:0;padding:0;box-sizing:border-box}
html,body{width:800px;height:1200px;overflow:hidden}
body{background:var(--page);font-family:"Source Sans 3",sans-serif;color:var(--ink);position:relative}

.brand{position:absolute;left:72px;top:36px;width:224px;text-align:center}
.brand-name{font-family:"Tinos",serif;font-size:21px;line-height:24px;color:var(--wine);display:flex;align-items:center;justify-content:center;gap:6px;white-space:nowrap}
.brand-mark{width:11px;height:11px;border-radius:50%;background:var(--wine);flex:none}
.brand-tag{font-size:8px;color:var(--wine);line-height:10px;margin-top:10px}

.search{position:absolute;left:581px;top:21px;width:143px;height:25px;background:#fff;border:1px solid #e2e2e2;border-radius:4px;font-size:8.5px;color:#555;padding:7px 0 0 13px}
.search svg{position:absolute;right:11px;top:6px}
.call{position:absolute;left:570px;top:61px;font-size:15px;color:var(--wine)}

.nav{position:absolute;background:var(--wine);display:flex;align-items:center;justify-content:space-around;font-size:10.5px;color:#fff}
.nav-main{left:66px;top:94px;width:668px;height:34px;border-radius:3px 3px 0 0;padding:0 12px}
.nav-sub{left:230px;top:128px;width:504px;height:29px;border-radius:0 0 3px 3px;padding:0 6px}

.hero{position:absolute;left:66px;top:128px;width:668px;height:302px;background:var(--panel);border:1px solid #e4e4e4;border-top:none;border-radius:0 0 3px 3px}
.hero-text{position:absolute;left:36px;top:110px;width:356px;text-align:center;color:var(--wine);font-family:"Tinos",serif}
.hero-title{font-size:16.5px;line-height:20px;white-space:nowrap}
.hero-line{font-size:11.5px;margin-top:9px;white-space:nowrap}
.hero-photo{position:absolute;left:394px;top:36px;width:232px;height:256px;background:radial-gradient(ellipse at 50% 45%,#d7c2ae 0%,#e9ddd0 45%,#ffffff 75%)}
.dots{position:absolute;left:24px;top:273px;display:flex;gap:4px}
.dots span{width:10px;height:10px;border-radius:50%;background:var(--dot)}
.dots span.on{background:var(--wine)}

.welcome{position:absolute;left:66px;top:442px;width:668px;text-align:center;color:var(--wine)}
.welcome h1{font-family:"Tinos",serif;font-weight:400;font-size:21px}
.welcome p{font-size:8.8px;line-height:11.5px;margin-top:8px}
.btn{display:inline-block;margin-top:8px;width:68px;height:20px;line-height:20px;background:var(--wine);color:#fff;font-size:8.5px;border-radius:3px}

.mission{position:absolute;left:66px;top:546px;width:668px;height:47px;background:#efefef;border:1px solid #e0e0e0;border-radius:3px;display:flex;align-items:center}
.mission h2{font-family:"Tinos",serif;font-weight:400;font-size:15px;color:#444;margin-left:49px;width:131px}
.mission p{font-size:8.5px;line-height:11px;color:var(--muted);width:485px}

.card{position:absolute;width:190px;background:var(--panel);border:1px solid var(--line);border-radius:0 0 3px 3px}
.card h3{height:28px;background:var(--wine);color:#fff;font-family:"Tinos",serif;font-weight:400;font-size:16px;text-align:center;line-height:28px;white-space:nowrap}
.card-img{height:82px}
.card ul{list-style:none;margin:11px 0 0 10px;font-size:8.5px;line-height:11px;color:var(--wine)}
.card li{padding-left:10px;position:relative}
.card li::before{content:"";position:absolute;left:0;top:3px;border-left:3px solid var(--wine);border-top:2.5px solid transparent;border-bottom:2.5px solid transparent}
.card li.cont::before{display:none}
.card p{font-size:8.5px;line-height:11px;color:var(--ink);margin:5px 10px 0 11px}
.c1{left:93px}.c2{left:306px}.c3{left:521px}
.r1{top:601px;height:207px}.r2{top:835px;height:207px}

.foot-nav{position:absolute;left:66px;width:668px;display:flex;justify-content:center;gap:14px;font-size:10.5px;color:var(--wine)}
.fn1{top:1079px}.fn2{top:1103px}
.social{position:absolute;left:349px;top:1131px;display:flex;gap:4px}
.social span{width:23px;height:23px;border-radius:50%;background:#2f5c9e}
.social span:nth-child(2){background:#3aa3dc}
.social span:nth-child(3){background:#c8352a}
.social span:nth-child(4){background:#2a7fb8}
.footer{position:absolute;left:66px;top:1169px;width:668px;height:31px;background:#ececec;border:1px solid #dcdcdc;border-bottom:none;border-radius:3px 3px 0 0;text-align:center;font-size:7.5px;color:#555;padding-top:12px}
.code{position:absolute;left:760px;top:1171px;font-size:8px;color:#555}
</style>
</head>
<body>

<header>
  <div class="brand">
    <div class="brand-name"><span class="brand-mark"></span>Brightwell Supports</div>
    <div class="brand-tag">Building Abilities ~ Creating Opportunities ~ Developing<br>Relationships</div>
  </div>
  <div class="search">Search
    <svg width="13" height="13" viewBox="0 0 13 13" aria-hidden="true"><circle cx="7.5" cy="5.5" r="4" fill="none" stroke="#888" stroke-width="1.4"/><line x1="4.6" y1="8.4" x2="1.5" y2="11.5" stroke="#888" stroke-width="1.6"/></svg>
  </div>
  <div class="call">Call Us : 0800 555 0199</div>

  <nav class="nav nav-main">
    <span>Home</span><span>Available Services</span><span>Residential Program</span><span>Day/Employment Program</span><span>SLS Program</span><span>Become a Provider</span><span>Employee Resources</span>
  </nav>
  <section class="hero">
    <div class="hero-text">
      <div class="hero-title">BRIGHTWELL SUPPORT SERVICES</div>
      <div class="hero-line">Employment &nbsp; - &nbsp; Client Supports</div>
      <div class="hero-line">SLS Services &nbsp; - &nbsp; Residential Services &nbsp; - &nbsp; Work Crew/Day Program</div>
    </div>
    <div class="hero-photo" role="img" aria-label="Photo of a smiling group of staff and clients looking up at the camera"></div>
    <div class="dots"><span></span><span></span><span></span><span class="on"></span></div>
  </section>
  <nav class="nav nav-sub">
    <span>Meet Our Team!</span><span>Activity Calendar</span><span>Training Calendar</span><span>Contact Us</span><span>Location</span><span>Community Resources</span>
  </nav>
</header>

<main>
  <section class="welcome">
    <h1>Welcome Website</h1>
    <p>Brightwell Supports is an agency designed to creatively serve individuals with developmental disabilities in community-based settings throughout Colorado.<br>Brightwell Supports is an approved service agency through the Division of Developmental Disabilities.</p>
    <span class="btn">Read more</span>
  </section>

  <section class="mission">
    <h2>Mission Statement:</h2>
    <p>To promote relationships, attachment, positive boundaries, and resource development to create opportunities and improve the lives of people living with disabilities.</p>
  </section>

  <article class="card c1 r1">
    <h3>Employment</h3>
    <div class="card-img" role="img" aria-label="Photo of a job coach meeting a client at a desk" style="background:linear-gradient(135deg,#8a2a22,#b86a4a 50%,#5a3a30)"></div>
    <ul><li>Work Assessment Sites</li><li>Community Job Placement</li><li>Job Coaching</li><li>Employment Skill Development</li></ul>
    <p>Neque porro quisquam est, qui dolorem ipsum quia dolor sit amet, consectetur, adipisci velit.</p>
  </article>
  <article class="card c2 r1">
    <h3>Client Supports</h3>
    <div class="card-img" role="img" aria-label="Photo of two people shaking hands in an office" style="background:linear-gradient(90deg,#2e4670,#9fb0c4 55%,#e4e8ee)"></div>
    <ul><li>Integrated Treatment Plans</li><li>Behavioral Supports</li><li>Agency-Sponsored Activities</li></ul>
    <p>Neque porro quisquam est, qui dolorem ipsum quia dolor sit amet, consectetur, adipisci velit.</p>
  </article>
  <article class="card c3 r1">
    <h3>SLS Services</h3>
    <div class="card-img" role="img" aria-label="Photo of a man choosing between open doors in a field" style="background:linear-gradient(180deg,#b8c8d8,#dfe6ec 60%,#8fb26a)"></div>
    <ul><li>Mentorship</li><li>Respite</li><li>Enhanced Homemaker</li><li>Personal Care</li></ul>
    <p>Neque porro quisquam est, qui dolorem ipsum quia dolor sit amet, consectetur, adipisci velit.</p>
  </article>

  <article class="card c1 r2">
    <h3>Residential Services</h3>
    <div class="card-img" role="img" aria-label="Photo of a man overlooking a city skyline" style="background:linear-gradient(180deg,#c9ced3,#8c939b 60%,#5d646c)"></div>
    <ul><li>Host Homes</li><li>Supported Apartment Program</li><li class="cont">(PCA Model)</li></ul>
    <p>Neque porro quisquam est, qui dolorem ipsum quia dolor sit amet, consectetur, adipisci velit.</p>
  </article>
  <article class="card c2 r2">
    <h3>Work Crew/Day Program</h3>
    <div class="card-img" role="img" aria-label="Photo of three smiling young women together" style="background:linear-gradient(90deg,#cfd8dc,#d9b79a 50%,#e8e2d8)"></div>
    <ul><li>30 Hour Weekly Program</li><li>Small Group Programming</li><li>Incentive-based Program</li><li>Individualized Programming</li><li>1:1 Services Offered</li><li>Supported Employment Crews</li></ul>
    <p>Neque porro quisquam est, qui dolorem ...</p>
  </article>
  <article class="card c3 r2">
    <h3>Community Resources</h3>
    <div class="card-img" role="img" aria-label="Photo of a smiling woman with colleagues in an office" style="background:linear-gradient(90deg,#6b4a3a,#d7b9a2 40%,#e9edf1)"></div>
    <ul><li>Work Assessment Sites</li><li>Community Job Placement</li><li>Job Coaching</li><li>Employment Skill Development</li></ul>
    <p>Neque porro quisquam est, qui dolorem ipsum quia dolor sit amet, consectetur, adipisci velit.</p>
  </article>
</main>

<footer>
  <nav class="foot-nav fn1"><span>Home</span><span>Available Services</span><span>Residential Program</span><span>Day/Employment Program</span><span>SLS Program</span><span>Become a Provider</span><span>Employee Resources</span></nav>
  <nav class="foot-nav fn2"><span>Meet Our Team!</span><span>Activity Calendar</span><span>Training Calendar</span><span>Contact Us</span><span>Location</span><span>Community Resources</span></nav>
  <div class="social" aria-label="Social links"><span></span><span></span><span></span><span></span></div>
  <div class="footer">© 2014. www.brightwellsupports.example</div>
  <div class="code">M1</div>
</footer>

</body>
</html>
```